Brackwell Yard Services Flyer Design

I need a new flyer design for my business, Brackwell Yard Services. I’ll be providing my old flyer and logo as references. The new flyer should feature updated wording, contact information, logos, and photos, but still keep the original “What We Do” section and include the phrase “Don’t See? Just Ask!” somewhere near the services. The flyer needs to look great in black and white for door-to-door handouts but also be eye-catching and professional enough for social media use.

The updated content should include the headline “Transforming Outdoor Spaces with Hard Work & Precision” and highlight three main service areas: Landscaping Services (project-based landscaping to clean, prepare, and transform outdoor spaces with precision), Property Cleanup (quick hauls, debris removal, or full cleanouts—no job too big or small), and Ground Preparation (pad preparation, brush removal, and fire lines—making properties safe, functional, and project-ready).

Please also include a “Why Choose Us?” section that lists: Locally owned since 2022, Reliable & affordable – no corners cut, Professional results you can trust, LICENSED AND Insured, and Quality work / on time / references / flexible / follow-up.

At the bottom, include the contact details: Call or Text Today!
www.brackwellyard.example
| sales@brackwellyard.example
| (555) 014-7293

The overall design should be clean, professional, and easy to read with a layout that clearly shows what we offer. Use visuals that represent outdoor services, landscaping, and property cleanup/prep work. I want something that feels trustworthy, family-friendly, and modern.
Use the same photo of leaf clean up from the original flyer if possible.
Our company colors are also black and white. For the most part.

```html
<!DOCTYPE html>
<html lang="en">
<head>
<meta charset="utf-8">
<title>Brackwell Yard Services Flyer</title>
<link rel="stylesheet" href="https://fonts.googleapis.com/css2?family=Oswald:wght@500;600;700&family=Signika:wght@600&family=Source+Sans+3:wght@400&display=swap">
<style>
  :root {
    --orange: #f7941d;
    --black: #0a0a0a;
    --white: #ffffff;
    --ink: #1a1a1a;
    --page: #ffffff;
  }
  * { box-sizing: border-box; margin: 0; padding: 0; }
  html, body { width: 1200px; height: 761px; overflow: hidden; background: var(--page); }
  body { position: relative; font-family: "Source Sans 3", Arial, sans-serif; color: var(--ink); }

  .flyer {
    --accent: var(--orange);
    --band-text: var(--white);
    --tag-text: var(--orange);
    --tag-bg: var(--white);
    position: absolute; top: 0; width: 589px; height: 761px; overflow: hidden; background: var(--white);
  }
  .flyer--color { left: 0; }
  .flyer--mono { left: 611px; --accent: var(--black); --tag-text: var(--black); }

  .hero {
    position: absolute; left: 0; top: 0; width: 100%; height: 207px;
    background: linear-gradient(160deg, #2d3e63 0%, #6c6a5e 35%, #a29a88 55%, #3f4a66 80%, #8a7a5a 100%);
  }
  .flyer--mono .hero { background: linear-gradient(160deg, #2a2a2a 0%, #6a6a6a 35%, #a5a5a5 55%, #4a4a4a 80%, #7d7d7d 100%); }
  .hero__rule { position: absolute; left: 0; top: 207px; width: 100%; height: 6px; background: var(--accent); }

  .brand {
    position: absolute; right: 12px; top: 10px; width: 150px;
    display: flex; align-items: center; gap: 6px;
    font-family: "Oswald", sans-serif; font-weight: 700; color: var(--white);
    font-size: 15px; line-height: 1; text-transform: uppercase;
  }
  .brand__mark { width: 26px; height: 26px; background: var(--white); flex: none; }

  .headline {
    position: absolute; left: 0; top: 131px; width: 326px; text-align: center;
    font-family: "Oswald", sans-serif; font-weight: 700; font-size: 20px; line-height: 22px;
    color: var(--white); text-transform: uppercase; text-shadow: 0 1px 3px rgba(0,0,0,.6);
  }

  .tag {
    position: absolute; display: flex; align-items: center; justify-content: center;
    font-family: "Signika", sans-serif; font-weight: 600; line-height: 1;
  }
  .tag--services { left: 229px; top: 198px; width: 127px; height: 31px; background: var(--accent); color: var(--white); font-size: 21px; }
  .tag--whatwedo { left: 229px; top: 335px; width: 130px; height: 33px; background: var(--tag-bg); color: var(--tag-text); font-size: 21px; }
  .tag--why { left: 194px; top: 537px; width: 172px; height: 33px; background: var(--accent); color: var(--white); font-size: 21px; }

  .services { position: absolute; left: 0; top: 213px; width: 100%; height: 107px; }
  .service { position: absolute; top: 28px; }
  .service:nth-child(1) { left: 19px; width: 175px; }
  .service:nth-child(2) { left: 213px; width: 180px; }
  .service:nth-child(3) { left: 400px; width: 180px; }
  .service__title {
    font-family: "Oswald", sans-serif; font-weight: 500; font-size: 18px; line-height: 22px;
    color: var(--accent); text-transform: uppercase; white-space: nowrap; letter-spacing: -0.2px;
  }
  .service__text { margin-top: 6px; font-size: 11px; line-height: 14px; color: var(--ink); }

  .band { position: absolute; left: 0; top: 320px; width: 100%; height: 197px; background: var(--accent); color: var(--band-text); }
  .list-col { position: absolute; top: 62px; }
  .list-col:nth-of-type(1) { left: 42px; }
  .list-col:nth-of-type(2) { left: 228px; }
  .list-col:nth-of-type(3) { left: 357px; }
  .list-col__title {
    font-family: "Oswald", sans-serif; font-weight: 500; font-size: 18px; line-height: 22px;
    text-transform: uppercase; margin-bottom: 6px; white-space: nowrap;
  }
  .bullets { list-style: none; }
  .bullets li { display: flex; align-items: center; gap: 6px; font-size: 12px; line-height: 19.4px; white-space: nowrap; }
  .bullets li::before {
    content: ""; width: 10px; height: 10px; flex: none; background: currentColor;
    clip-path: polygon(25% 3%, 75% 3%, 100% 50%, 75% 97%, 25% 97%, 0 50%);
  }
  .band__ask {
    position: absolute; left: 0; top: 171px; width: 100%; text-align: center;
    font-family: "Oswald", sans-serif; font-weight: 500; font-size: 15px; text-transform: uppercase;
  }

  .photo { position: absolute; top: 517px; height: 194px; }
  .photo--leaves { left: 0; width: 171px; background: linear-gradient(170deg, #8a7a3a 0%, #a8903c 40%, #7b4a1e 75%, #5a3012 100%); }
  .photo--yard { left: 418px; width: 171px; background: linear-gradient(180deg, #9fb6cc 0%, #c8ced4 30%, #b8a58a 60%, #d6c4a4 100%); }
  .flyer--mono .photo--leaves { background: linear-gradient(170deg, #7a7a7a 0%, #9a9a9a 40%, #555 75%, #3a3a3a 100%); }
  .flyer--mono .photo--yard { background: linear-gradient(180deg, #c8c8c8 0%, #bdbdbd 30%, #9e9e9e 60%, #d0d0d0 100%); }

  .why { position: absolute; left: 171px; top: 517px; width: 247px; height: 194px; }
  .why .bullets { position: absolute; left: 31px; top: 61px; }
  .why .bullets li { color: var(--accent); }
  .why .bullets li span { color: var(--ink); }
  .why__licensed {
    position: absolute; left: 0; top: 148px; width: 100%; text-align: center;
    font-family: "Oswald", sans-serif; font-weight: 500; font-size: 16px; color: var(--accent); text-transform: uppercase;
  }
  .why__perks {
    position: absolute; left: 0; top: 170px; width: 100%; text-align: center;
    font-family: "Oswald", sans-serif; font-weight: 500; font-size: 10.5px; color: var(--ink); white-space: nowrap;
  }
  .why__perks i { font-style: normal; color: var(--accent); padding: 0 2px; }

  .footer { position: absolute; left: 0; top: 711px; width: 100%; height: 50px; background: var(--black); }
  .flyer--color .footer { --foot: var(--orange); }
  .flyer--mono .footer { --foot: var(--white); }
  .footer__cta {
    position: absolute; left: 0; top: 2px; width: 100%; text-align: center;
    font-family: "Oswald", sans-serif; font-weight: 600; font-size: 19px; line-height: 24px; color: var(--foot);
  }
  .contacts {
    position: absolute; left: 0; top: 28px; width: 100%; display: flex; justify-content: center; gap: 12px;
    font-family: "Oswald", sans-serif; font-weight: 500; font-size: 12.5px; line-height: 18px; color: var(--foot);
  }
  .contact { display: flex; align-items: center; gap: 4px; white-space: nowrap; }
  .contact svg { width: 14px; height: 14px; fill: none; stroke: currentColor; stroke-width: 1.3; }
</style>
</head>
<body>

<!-- Colour edition -->
<article class="flyer flyer--color">
  <div class="hero" role="img" aria-label="Photo of a blue dumpster trailer loaded with carpet, hoses and household debris"></div>
  <div class="hero__rule"></div>
  <div class="brand"><span class="brand__mark"></span><span>Brackwell Yard Services</span></div>
  <h1 class="headline">Transforming Outdoor Spaces<br>With Hard Work &amp; Precision</h1>

  <section class="services">
    <div class="service"><h2 class="service__title">Landscaping Services</h2><p class="service__text">Project-based landscaping to clean, prepare, and transform outdoor spaces with precision.</p></div>
    <div class="service"><h2 class="service__title">Ground Preparation</h2><p class="service__text">Pad preparation, brush removal, and fire lines—making properties safe, functional, and project-ready.</p></div>
    <div class="service"><h2 class="service__title">Property Cleanup</h2><p class="service__text">Quick hauls, debris removal, or full cleanouts—no job too big or small.</p></div>
  </section>
  <div class="tag tag--services">Our Services</div>

  <section class="band">
    <div class="list-col"><h3 class="list-col__title">Remove</h3><ul class="bullets"><li>Junk removal</li><li>Trash &amp; waste hauling</li><li>Yard &amp; garden cleanup</li><li>Appliance removal</li></ul></div>
    <div class="list-col"><h3 class="list-col__title">Install</h3><ul class="bullets"><li>Mulch</li><li>DG</li><li>Plants</li><li>Rock</li></ul></div>
    <div class="list-col"><h3 class="list-col__title">Maintenance &amp; Other</h3><ul class="bullets"><li>Yard cleanup</li><li>Weed prevention (pre-emergent)</li><li>Roof &amp; gutter cleaning</li><li>Fence &amp; deck staining</li></ul></div>
    <p class="band__ask">Don’t See? Just Ask!</p>
  </section>
  <div class="tag tag--whatwedo">What We Do</div>

  <div class="photo photo--leaves" role="img" aria-label="Photo of a rake leaning on a full bag of autumn leaves on a lawn"></div>
  <section class="why">
    <ul class="bullets"><li><span>Locally owned since 2022</span></li><li><span>Reliable &amp; affordable – no corners cut</span></li><li><span>Professional results you can trust</span></li></ul>
    <p class="why__licensed">Licensed and Insured</p>
    <p class="why__perks">Quality work<i>•</i>On Time<i>•</i>References<i>•</i>Flexible<i>•</i>Follow-up</p>
  </section>
  <div class="tag tag--why">Why Choose Us?</div>
  <div class="photo photo--yard" role="img" aria-label="Photo of a finished backyard with gravel bed, block retaining edge and wooden fence"></div>

  <footer class="footer">
    <p class="footer__cta">CALL OR TEXT TODAY!</p>
    <div class="contacts">
      <span class="contact"><svg viewBox="0 0 16 16"><circle cx="8" cy="8" r="6.5"/><ellipse cx="8" cy="8" rx="3" ry="6.5"/><path d="M1.5 8h13M2.5 4.5h11M2.5 11.5h11"/></svg>www.brackwellyard.example</span>
      <span class="contact"><svg viewBox="0 0 16 16"><rect x="1.5" y="3.5" width="13" height="9"/><path d="M1.5 3.5l6.5 5 6.5-5"/></svg>sales@brackwellyard.example</span>
      <span class="contact"><svg viewBox="0 0 16 16"><path d="M4 1.8l2 3-1.2 1.4c.8 1.8 2.2 3.2 4 4l1.4-1.2 3 2-1 2.2c-5 .4-10.4-5-10-10z"/></svg>(555) 014-7293</span>
    </div>
  </footer>
</article>

<!-- Black and white edition -->
<article class="flyer flyer--mono">
  <div class="hero" role="img" aria-label="Black and white photo of a dumpster trailer loaded with carpet, hoses and household debris"></div>
  <div class="hero__rule"></div>
  <div class="brand"><span class="brand__mark"></span><span>Brackwell Yard Services</span></div>
  <h1 class="headline">Transforming Outdoor Spaces<br>With Hard Work &amp; Precision</h1>

  <section class="services">
    <div class="service"><h2 class="service__title">Landscaping Services</h2><p class="service__text">Project-based landscaping to clean, prepare, and transform outdoor spaces with precision.</p></div>
    <div class="service"><h2 class="service__title">Ground Preparation</h2><p class="service__text">Pad preparation, brush removal, and fire lines—making properties safe, functional, and project-ready.</p></div>
    <div class="service"><h2 class="service__title">Property Cleanup</h2><p class="service__text">Quick hauls, debris removal, or full cleanouts—no job too big or small.</p></div>
  </section>
  <div class="tag tag--services">Our Services</div>

  <section class="band">
    <div class="list-col"><h3 class="list-col__title">Remove</h3><ul class="bullets"><li>Junk removal</li><li>Trash &amp; waste hauling</li><li>Yard &amp; garden cleanup</li><li>Appliance removal</li></ul></div>
    <div class="list-col"><h3 class="list-col__title">Install</h3><ul class="bullets"><li>Mulch</li><li>DG</li><li>Plants</li><li>Rock</li></ul></div>
    <div class="list-col"><h3 class="list-col__title">Maintenance &amp; Other</h3><ul class="bullets"><li>Yard cleanup</li><li>Weed prevention (pre-emergent)</li><li>Roof &amp; gutter cleaning</li><li>Fence &amp; deck staining</li></ul></div>
    <p class="band__ask">Don’t See? Just Ask!</p>
  </section>
  <div class="tag tag--whatwedo">What We Do</div>

  <div class="photo photo--leaves" role="img" aria-label="Black and white photo of a rake leaning on a full bag of leaves on a lawn"></div>
  <section class="why">
    <ul class="bullets"><li><span>Locally owned since 2022</span></li><li><span>Reliable &amp; affordable – no corners cut</span></li><li><span>Professional results you can trust</span></li></ul>
    <p class="why__licensed">Licensed and Insured</p>
    <p class="why__perks">Quality work<i>•</i>On Time<i>•</i>References<i>•</i>Flexible<i>•</i>Follow-up</p>
  </section>
  <div class="tag tag--why">Why Choose Us?</div>
  <div class="photo photo--yard" role="img" aria-label="Black and white photo of a finished backyard with gravel bed, block edge and wooden fence"></div>

  <footer class="footer">
    <p class="footer__cta">CALL OR TEXT TODAY!</p>
    <div class="contacts">
      <span class="contact"><svg viewBox="0 0 16 16"><circle cx="8" cy="8" r="6.5"/><ellipse cx="8" cy="8" rx="3" ry="6.5"/><path d="M1.5 8h13M2.5 4.5h11M2.5 11.5h11"/></svg>www.brackwellyard.example</span>
      <span class="contact"><svg viewBox="0 0 16 16"><rect x="1.5" y="3.5" width="13" height="9"/><path d="M1.5 3.5l6.5 5 6.5-5"/></svg>sales@brackwellyard.example</span>
      <span class="contact"><svg viewBox="0 0 16 16"><path d="M4 1.8l2 3-1.2 1.4c.8 1.8 2.2 3.2 4 4l1.4-1.2 3 2-1 2.2c-5 .4-10.4-5-10-10z"/></svg>(555) 014-7293</span>
    </div>
  </footer>
</article>

</body>
</html>
```